Business Card Design for Training Business

Clear Path Coaching is a new business that delivers training and other services with a focus on topics related to mental health and wellbeing, for example, Wellmind Response Course, Resilience etc. We have a strong focus on evidence-based psychology and neuroscience. I have a logo which I will upload with the brief, so please consider colours that work well with the logo.
Target Market(s)
Adults, workplaces (particularly government and not-for-profits)
Industry/Entity Type
Business
Contact Information for Business Card
Head Strong TrainingSamantha SellwoodDirector0438 770 850sam@headstrongtraining.com.auwww.headstrongtraining.com.au

```html
<!DOCTYPE html>
<html lang="en">
<head>
<meta charset="utf-8">
<title>Clear Path Coaching – Business Card</title>
<link rel="stylesheet" href="https://fonts.googleapis.com/css2?family=Open+Sans:wght@300;400;700&display=swap">
<style>
  :root {
    --page-bg: #e9e6e2;
    --card-top: #6b625d;
    --card-bottom: #4e4642;
    --teal: #2fb5b8;
    --light-bar: #dedede;
    --text-light: #f2f0ee;
    --text-soft: #d4cfcb;
    --rule: #bdb6b1;
  }
  * { margin: 0; padding: 0; box-sizing: border-box; }
  html, body {
    width: 1200px;
    height: 1022px;
    overflow: hidden;
    background: var(--page-bg);
    font-family: "Open Sans", Arial, sans-serif;
  }
  .stage {
    width: 1200px;
    height: 1022px;
    display: flex;
    align-items: center;
    justify-content: center;
  }
  .card {
    position: relative;
    width: 900px;
    height: 514px;
    border-radius: 22px;
    background: linear-gradient(160deg, var(--card-top), var(--card-bottom));
    box-shadow: 0 18px 40px rgba(0,0,0,0.25);
    overflow: hidden;
  }
  .brand {
    position: absolute;
    left: 60px;
    top: 150px;
    width: 330px;
    display: flex;
    align-items: center;
    gap: 22px;
  }
  .brand-mark {
    flex: none;
    width: 100px;
    height: 100px;
    border-radius: 50%;
    border: 3px solid var(--teal);
  }
  .brand-name {
    color: var(--text-soft);
    font-weight: 300;
    font-size: 24px;
    letter-spacing: 3px;
    line-height: 1.3;
    text-transform: uppercase;
    white-space: nowrap;
  }
  .person-name {
    position: absolute;
    right: 58px;
    top: 112px;
    color: var(--text-light);
    font-weight: 700;
    font-size: 34px;
    white-space: nowrap;
  }
  .title-row {
    position: absolute;
    left: 420px;
    right: 58px;
    top: 162px;
    display: flex;
    align-items: center;
    gap: 10px;
  }
  .title-rule {
    flex: 1;
    height: 1px;
    background: var(--rule);
  }
  .job-title {
    color: var(--teal);
    font-weight: 300;
    font-size: 24px;
  }
  .contact {
    position: absolute;
    left: 420px;
    top: 300px;
    list-style: none;
  }
  .contact li {
    display: flex;
    align-items: center;
    gap: 14px;
    color: var(--text-light);
    font-size: 21px;
    line-height: 34px;
    white-space: nowrap;
  }
  .contact svg { width: 17px; height: 17px; flex: none; }
  .accent-bar {
    position: absolute;
    left: 300px;
    bottom: 0;
    width: 62px;
  }
  .accent-bar .light { height: 14px; background: var(--light-bar); }
  .accent-bar .teal { height: 62px; background: var(--teal); }
</style>
</head>
<body>
<div class="stage">
  <div class="card">
    <div class="brand">
      <div class="brand-mark"></div>
      <div class="brand-name">Clear Path<br>Coaching</div>
    </div>

    <div class="person-name">Rebecca Tanfield</div>
    <div class="title-row">
      <span class="title-rule"></span>
      <span class="job-title">Director</span>
    </div>

    <ul class="contact">
      <li>
        <svg viewBox="0 0 24 24" fill="var(--teal)" aria-hidden="true"><path d="M6.6 10.8a15.1 15.1 0 0 0 6.6 6.6l2.2-2.2a1 1 0 0 1 1-.25 11.4 11.4 0 0 0 3.6.57 1 1 0 0 1 1 1V20a1 1 0 0 1-1 1A17 17 0 0 1 3 4a1 1 0 0 1 1-1h3.5a1 1 0 0 1 1 1c0 1.25.2 2.45.57 3.57a1 1 0 0 1-.25 1z"/></svg>
        0491 362 517
      </li>
      <li>
        <svg viewBox="0 0 24 24" fill="none" stroke="var(--teal)" stroke-width="2" aria-hidden="true"><rect x="3" y="5" width="18" height="14" rx="1"/><path d="M3 6l9 7 9-7"/></svg>
        bec@clearpathcoaching.example.au
      </li>
      <li>
        <svg viewBox="0 0 24 24" fill="none" stroke="var(--teal)" stroke-width="2" aria-hidden="true"><circle cx="12" cy="12" r="9"/><path d="M3 12h18M12 3c3 3.5 3 14.5 0 18M12 3c-3 3.5-3 14.5 0 18"/></svg>
        www.clearpathcoaching.example.au
      </li>
    </ul>

    <div class="accent-bar">
      <div class="light"></div>
      <div class="teal"></div>
    </div>
  </div>
</div>
</body>
</html>
```